Business card design for a dynamic IT consulting company

We need a business card design for a young firm, specialized in the Telecommunications/Consulting industry. The name of the company is Quindor and Partners Business Consulting Ltd. (Short name: Quindor and Partnes)
Quindor = solve read reverse, so we aim to be uncomplicated and solution-oriented. The small pipe in our logo is also related to the word solve. So we need a new business card design, which is simple, eye catching and something non traditional (I would probably prefer a square shaped design rather than a rectangle, but open for suggestions). Attached our logo.

Target Market(s)

Usually our customers are Tier1 Telecoms providers (Q-Netra, Palorix, etc) and their executives.

Industry/Entity Type

Business

Contact Information for Business Card

Name: Bence Tolnavari
Email: b.tolnavari@quindor.hu
Web: www.quindor.hu
Mobile: +36 30 518 2769
Title: Managing Director

Optional:
Company name: Quindor and Partners Ltd.
Address: 1087 Budapest, Tolvenka str. 28/C, Hungary

Font styles to use
Other font styles liked:
• helveticaneue_medium, Prime Regular are used now.

Colors

Designer to choose colors to be used in the design.

Requirements
Must have
• I would like to have a 2 sided design.
Nice to have
• I thought if we make the logo a bit bigger (without the company name), that could go to the back with the company name below. I though, if the pipe in the logo is somehow touchable on the business card, would be nice and unique.

```html
<!DOCTYPE html>
<html lang="en">
<head>
<meta charset="utf-8">
<title>Quindor and Partners – Business Card</title>
<link rel="stylesheet" href="https://fonts.googleapis.com/css2?family=Arimo:wght@400;700&display=swap">
<style>
  :root {
    --backdrop: #5a4838;
    --paper: #f3f3f3;
    --slate: #5d5e60;
    --ink-grey: #5a5a5c;
    --brand-blue: #0a94d4;
    --brand-magenta: #a3268e;
    --white: #ffffff;
    --faint-blue: #cfe6f2;
    --faint-pink: #efd6e8;
  }
  html, body {
    margin: 0;
    width: 1200px;
    height: 960px;
    overflow: hidden;
    background: var(--backdrop);
  }
  .stage {
    position: relative;
    width: 1200px;
    height: 960px;
  }
  .card {
    position: absolute;
    top: 309px;
    width: 342px;
    height: 343px;
    background: var(--paper);
    overflow: hidden;
    font-family: "Arimo", Helvetica, Arial, sans-serif;
  }
  .card--front { left: 235px; }
  .card--back { left: 623px; }

  .card__chevron {
    position: absolute;
    inset: 0;
  }

  .company {
    position: absolute;
    left: 0;
    right: 0;
    margin: 0;
    text-align: center;
    font-family: "Arimo", Helvetica, Arial, sans-serif;
    font-weight: 400;
    color: var(--ink-grey);
    white-space: nowrap;
    line-height: 1;
  }
  .company__square {
    display: inline-block;
    width: 11px;
    height: 11px;
    margin-right: 8px;
    background: var(--brand-blue);
    vertical-align: 1px;
  }
  .card--front .company { top: 42px; font-size: 20px; }
  .card--back .company { top: 32px; font-size: 27px; }

  .person {
    position: absolute;
    top: 98px;
    left: 0;
    right: 0;
    text-align: center;
  }
  .person__name {
    margin: 0;
    font-size: 18px;
    font-weight: 700;
    color: var(--brand-blue);
    letter-spacing: 0.2px;
  }
  .person__title {
    margin: 2px 0 0;
    font-size: 14px;
    color: var(--ink-grey);
    letter-spacing: 0.3px;
  }

  .contact {
    position: absolute;
    top: 240px;
    left: 0;
    right: 0;
    text-align: center;
    color: var(--white);
    font-size: 13.5px;
    line-height: 18px;
    font-style: normal;
  }
  .contact p { margin: 0; }
  .contact__reach { margin-top: 8px !important; }

  .web {
    position: absolute;
    top: 74px;
    left: 0;
    right: 0;
    text-align: center;
    margin: 0;
    font-size: 14px;
    letter-spacing: 8.6px;
    color: var(--ink-grey);
  }
  .back-decor {
    position: absolute;
    left: 30px;
    top: 112px;
    width: 280px;
    height: 210px;
    background: linear-gradient(135deg, var(--faint-pink) 0%, #ececec 45%, var(--faint-blue) 100%);
    opacity: 0.6;
  }
</style>
</head>
<body>
<main class="stage">

  <section class="card card--front" aria-label="Business card, front">
    <svg class="card__chevron" width="342" height="343" viewBox="0 0 342 343" aria-hidden="true">
      <polygon points="0,110 170,228 342,110 342,343 0,343" fill="var(--slate)"/>
      <polyline points="0,104 170,222 342,104" fill="none" stroke="var(--white)" stroke-width="3"/>
      <polyline points="0,99 170,217" fill="none" stroke="var(--brand-magenta)" stroke-width="4"/>
      <polyline points="170,217 342,99" fill="none" stroke="var(--brand-blue)" stroke-width="4"/>
    </svg>

    <p class="company"><span class="company__square"></span>Quindor and Partners</p>

    <div class="person">
      <h1 class="person__name">BENCE TOLNAVARI</h1>
      <p class="person__title">MANAGING DIRECTOR</p>
    </div>

    <address class="contact">
      <p>Quindor and Partners Ltd.,1087 Budapest</p>
      <p>Tolvenka str. 28/C, Hungary</p>
      <p class="contact__reach">+36 30 518 2769</p>
      <p>b.tolnavari@quindor.hu</p>
    </address>
  </section>

  <section class="card card--back" aria-label="Business card, back">
    <p class="company">Quindor and Partners</p>
    <p class="web">www.quindor.hu</p>
    <div class="back-decor" role="img" aria-label="Faint decorative pattern of pastel pink, blue and grey tiles"></div>
  </section>

</main>
</body>
</html>
```